Children’s entertainer/balloon artist Website Home Page and custom landing page

I need a home page design for the home page of a children and family entertainer/balloon twister’s website. I also need a custom landing page for family theatre shows performed by the same entertainer.
It will be a Wordpress website and I need the final artwork in a layer Photoshop file with all the layers clearly named and labeled.

Target Market(s)

The site visitors are mainly mums, aged between early 20’s and late 30’s. Other visitors will included companies for Christmas functions, and event organisers for corporate functions.

Industry/Entity Type

Entertainment

Number of Pages Required

2 page

Font styles to use
Sans Serif

Colors
34a6d7
f37122

Requirements
Must have
• Layout
• I have included a wireframe for the home page layout and the custom landing page for your reference. This is a guide only and I welcome your interpretation with the rough layout provided.
• This website needs to look good on all devices as it will be fully responsive.
• It needs to include a footer area on the page, that has social media and a call to action area included.
• Colours
• The main colours for the site is:
• orange (call to action colour)
• ff6800
• blue/turquoise
• 42abc3
• Pictures
• I have included images of the entertainer/balloon artist for you to use/take inspiration from.
• These images will be included on the website. I want to show lots of people having fun.
• I would like to have elements of the logo used in isolation across the website
• i.e. the octopus figure to be included in the footer or the bird element to be included in the testimonial slider etc.
• Elements to include
• Note: use the images of the entertainer in the boxes on the home page (balloon shows, balloon twisting, balloon workshops, theatre shows (the three little balloon pigs on his head)
Nice to have
Should not have
• Element to avoid
• Stock imagery of balloon sculptures - use images provided.

```html
<!DOCTYPE html>
<html lang="en">
<head>
<meta charset="utf-8">
<title>Benny – Theater Artist, Balloon Artist, Kids Entertainer</title>
<link href="https://fonts.googleapis.com/css2?family=Oswald:wght@400;500;700&family=Open+Sans:wght@400;600;700&display=swap" rel="stylesheet">
<style>
:root{
  --orange:#ff6800;
  --blue:#42abc3;
  --dark:#1f1f1f;
  --darker:#141414;
  --parch:#e9dcc0;
  --ink:#3a2f22;
  --muted:#6b5f4f;
  --white:#ffffff;
}
*{box-sizing:border-box;margin:0;padding:0}
html,body{width:1200px;height:2588px;overflow:hidden}
body{position:relative;font-family:"Open Sans",Arial,sans-serif;color:var(--ink);background:var(--parch)}
.abs{position:absolute}
.topnav{left:0;top:0;width:1200px;height:32px;background:var(--darker);display:flex;align-items:center;padding-left:80px;gap:34px}
.topnav a{font-family:"Oswald",sans-serif;font-size:14px;color:var(--white);text-decoration:none;letter-spacing:.5px}
.topnav a.active{border-bottom:2px solid var(--orange)}
.hero{left:0;top:32px;width:1200px;height:696px;background:radial-gradient(ellipse at 40% 45%,#c0201f 0%,#8e0d12 45%,#3d0406 100%)}
.hero-valance{left:0;top:32px;width:1200px;height:70px;background:linear-gradient(#5a0507,#a3161a)}
.brand{left:0;width:900px;top:250px;display:flex;justify-content:center;align-items:center;gap:10px}
.brand-mark{width:26px;height:26px;border-radius:50%;background:var(--blue)}
.brand-name{font-family:"Oswald",sans-serif;font-weight:500;font-size:22px;color:var(--white)}
.hero-name{left:0;width:900px;top:430px;text-align:center;font-family:"Oswald",sans-serif;font-weight:700;font-size:64px;line-height:80px;color:var(--white);letter-spacing:3px;text-shadow:0 3px 6px rgba(0,0,0,.5)}
.hero-tag{left:0;width:900px;top:518px;text-align:center;font-size:20px;font-weight:600;color:var(--white)}
.btn{display:inline-block;background:var(--orange);color:var(--white);font-family:"Oswald",sans-serif;font-size:15px;text-align:center;border:2px solid var(--white)}
.hero-btn{left:380px;top:596px;width:140px;height:40px;line-height:36px}
.performer{left:750px;top:380px;width:400px;height:348px;background:linear-gradient(#7fb6d9,#3b79b0);border-radius:180px 180px 0 0}
.about{left:0;top:728px;width:1200px;height:352px;background:linear-gradient(#ddc9a0,var(--parch),#d6c298)}
.h2{font-family:"Oswald",sans-serif;font-size:28px;color:var(--ink);letter-spacing:.5px}
.h2 em{font-style:normal;color:var(--orange)}
.about-title{left:70px;top:774px}
.rule{height:2px;background:var(--muted);opacity:.5}
.about-text{left:70px;top:836px;width:640px;font-size:13px;line-height:20px;color:var(--muted)}
.read{left:70px;top:1018px;width:80px;height:28px;line-height:28px;font-size:12px;background:var(--dark);color:var(--white);text-align:center;font-family:"Oswald",sans-serif}
.film{left:740px;top:788px;width:270px;height:262px;background:#111;padding:18px 10px}
.film-photo{width:100%;height:100%;background:linear-gradient(135deg,#d7432e,#f0c23c,#3d8ed0)}
.cols{left:0;top:1080px;width:1200px;height:500px;background:var(--parch)}
.col-title{font-family:"Oswald",sans-serif;font-size:22px}
.col-title em{font-style:normal;color:var(--orange)}
.cal{left:70px;top:1196px;width:330px;background:var(--white);box-shadow:0 2px 6px rgba(0,0,0,.25)}
.cal-head{background:var(--orange);color:var(--white);font-family:"Oswald",sans-serif;font-size:22px;text-align:center;height:48px;line-height:48px}
.cal table{width:100%;border-collapse:collapse;font-size:12px;text-align:center}
.cal th{font-weight:700;padding:8px 0;color:var(--ink)}
.cal td{padding:8px 0;color:var(--muted)}
.cal td.on{background:var(--orange);color:var(--white)}
.news{left:475px;top:1200px;width:330px}
.news-item{display:flex;gap:12px;margin-bottom:20px}
.thumb{width:70px;height:62px;flex:none;background:linear-gradient(135deg,#4f7fbf,#e0913b)}
.news-item h4{font-size:14px;color:var(--ink)}
.news-item p{font-size:11px;color:var(--muted);line-height:16px}
.news-item span{color:var(--orange)}
.view{left:720px;top:1460px;font-size:12px;font-weight:700;color:var(--orange)}
.arrows{left:760px;top:1154px;display:flex;gap:4px}
.arrows i{display:block;width:18px;height:18px;background:var(--dark)}
.signup{left:860px;top:1200px;width:270px;font-size:12px;line-height:17px;color:var(--muted)}
.field{height:34px;background:var(--white);border:1px solid #ccc;padding:8px 10px;font-size:11px;color:#999;margin-top:10px}
.submit{margin-top:12px;width:84px;height:32px;line-height:28px;font-size:13px}
.testi{left:0;top:1580px;width:1200px;height:324px;background:linear-gradient(#d9c59b,var(--parch))}
.testi-title{left:0;width:1200px;top:1596px;text-align:center}
.avatar{left:560px;top:1664px;width:80px;height:80px;border-radius:50%;background:linear-gradient(#9fb6c8,#4b6680);border:3px solid var(--white)}
.quote{left:200px;width:800px;top:1764px;text-align:center;font-size:14px;line-height:22px;color:var(--muted)}
.quote b{display:block;color:var(--ink);font-size:14px;font-style:italic;margin-bottom:6px}
.author{left:0;width:1200px;top:1858px;text-align:center;font-size:13px;color:var(--ink)}
.author b{font-weight:700}
.contact{left:0;top:1904px;width:1200px;height:512px;background:var(--orange)}
.contact-title{left:0;width:1200px;top:1948px;text-align:center;color:var(--white)}
.contact-title em{font-style:normal;color:var(--dark)}
.inp{border:1px solid rgba(255,255,255,.7);color:var(--white);font-size:12px;padding:10px 14px;height:36px}
.cbtn{height:32px;line-height:30px;border:1px solid var(--white);color:var(--white);font-family:"Oswald",sans-serif;font-size:13px;text-align:center}
.info{left:850px;display:flex;align-items:center;gap:20px;color:var(--white);font-size:14px}
.info-ico{width:50px;height:50px;border-radius:50%;background:var(--dark);display:flex;align-items:center;justify-content:center;flex:none}
.footer{left:0;top:2416px;width:1200px;height:172px;background:var(--dark)}
.fnav{left:0;width:1200px;top:2445px;display:flex;justify-content:center;gap:36px}
.fnav a{color:var(--white);font-family:"Oswald",sans-serif;font-size:14px;text-decoration:none}
.social{left:0;width:1200px;top:2495px;display:flex;justify-content:center;gap:12px}
.social i{display:block;width:32px;height:32px;border:1px solid #777;background:#2b2b2b}
.copy{left:0;top:2550px;width:1200px;height:38px;background:var(--darker);color:#aaa;font-size:12px;text-align:center;line-height:38px}
</style>
</head>
<body>
<nav class="abs topnav">
  <a class="active">HOME</a><a>ABOUT ME</a><a>CORPORATE SHOWS</a><a>PRIVATE FUNCTIONS</a><a>DIRECTING</a><a>REVIEWS</a><a>CONTACT ME</a>
</nav>

<div class="abs hero" role="img" aria-label="Red theatre stage curtains with spotlights"></div>
<div class="abs hero-valance"></div>
<div class="abs brand"><span class="brand-mark"></span><span class="brand-name">Pop &amp; Twist Shows</span></div>
<div class="abs hero-name">BENNY</div>
<div class="abs hero-tag">Theater Artist &nbsp;•&nbsp; Balloon Artist &nbsp;•&nbsp; Kids Entertainer</div>
<a class="abs btn hero-btn">BOOK ME NOW</a>
<div class="abs performer" role="img" aria-label="The entertainer in a blue suit holding a microphone stand"></div>

<section class="abs about"></section>
<h2 class="abs h2 about-title">ABOUT MY <em>THEATER PERFORMANCE</em></h2>
<div class="abs rule" style="left:490px;top:796px;width:220px"></div>
<p class="abs about-text">Lorem ipsum dolor sit amet, consectetur adipiscing elit, sed diam nonummy nibh euismod tincidunt ut laoreet dolore magna aliquam erat volutpat. Ut wisi enim ad minim veniam, quis nostrud exerci tation ullamcorper suscipit lobortis nisl ut aliquip ex ea commodo consequat. Duis autem vel eum iriure dolor in hendrerit in vulputate velit esse molestie consequat, vel illum dolore eu feugiat nulla facilisis at vero eros et accumsan et iusto odio dignissim qui blandit praesent luptatum zzril delenit augue duis dolore te feugait nulla facilisi.</p>
<a class="abs read">READ ALL</a>
<div class="abs film"><div class="film-photo" role="img" aria-label="Photo of the entertainer with balloon sculptures at a theatre show"></div></div>

<section class="abs cols"></section>
<h3 class="abs col-title" style="left:70px;top:1150px">UPCOMING <em>EVENTS</em></h3>
<div class="abs cal">
  <div class="cal-head">OCTOBER 2015</div>
  <table>
    <tr><th>SUN</th><th>MON</th><th>TUE</th><th>WED</th><th>THR</th><th>FRI</th><th>SAT</th></tr>
    <tr><td></td><td></td><td></td><td></td><td>1</td><td>2</td><td>3</td></tr>
    <tr><td>4</td><td>5</td><td>6</td><td>7</td><td>8</td><td>9</td><td>10</td></tr>
    <tr><td>11</td><td>12</td><td>13</td><td>14</td><td>15</td><td>16</td><td>17</td></tr>
    <tr><td>18</td><td>19</td><td>20</td><td>21</td><td>22</td><td class="on">23</td><td>24</td></tr>
    <tr><td>25</td><td>26</td><td>27</td><td>28</td><td class="on">29</td><td>30</td><td>31</td></tr>
  </table>
</div>
<h3 class="abs col-title" style="left:475px;top:1150px">LATEST <em>NEWS</em></h3>
<div class="abs arrows"><i></i><i></i></div>
<div class="abs news">
  <div class="news-item"><div class="thumb" role="img" aria-label="News photo"></div><div><h4>Lorem Ipsum Dolor</h4><p>By Person Name <span>(Read more)</span><br>Nam quam nunc blandit vel luctus.</p></div></div>
  <div class="news-item"><div class="thumb" role="img" aria-label="News photo"></div><div><h4>Lorem Ipsum Dolor</h4><p>By Person Name <span>(Read more)</span><br>Nam quam nunc blandit vel luctus.</p></div></div>
  <div class="news-item"><div class="thumb" role="img" aria-label="News photo"></div><div><h4>Lorem Ipsum Dolor</h4><p>By Person Name <span>(Read more)</span><br>Nam quam nunc blandit vel luctus.</p></div></div>
</div>
<a class="abs view">VIEW ALL &gt;&gt;</a>
<h3 class="abs col-title" style="left:860px;top:1150px">NEWSLETTER <em>SIGNUP</em></h3>
<div class="abs signup">
  <p>Signup To Our Newsletter For Weekly Updates, Fill The Form and it's done.</p>
  <div class="field">Type your Name</div>
  <div class="field">Type your Email</div>
  <div class="btn submit">SUBMIT</div>
</div>

<section class="abs testi"></section>
<h2 class="abs h2 testi-title">WHAT MY <em>CUSTOMERS</em> SAY</h2>
<div class="abs rule" style="left:230px;top:1618px;width:220px"></div>
<div class="abs rule" style="left:750px;top:1618px;width:220px"></div>
<div class="abs avatar" role="img" aria-label="Customer portrait"></div>
<svg class="abs" style="left:140px;top:1750px" width="20" height="30" viewBox="0 0 20 30"><path d="M16 3 4 15l12 12" fill="none" stroke="#3a2f22" stroke-width="4"/></svg>
<svg class="abs" style="left:1040px;top:1750px" width="20" height="30" viewBox="0 0 20 30"><path d="M4 3l12 12L4 27" fill="none" stroke="#3a2f22" stroke-width="4"/></svg>
<div class="abs quote"><b>Vestibulum porta, diam quis auctor sollicitudin, dui quam dapibus ligula, consectetur</b>Lorem ipsum dolor sit amet, consectetur adipiscing elit. Integer nec odio praesent libero sed cursus ante dapibus diam nulla quis sem at nibh elementum imperdiet duis sagittis ipsum mauris.</div>
<div class="abs author"><b>ELLA MORTON</b> | Party Planner</div>

<section class="abs contact"></section>
<h2 class="abs h2 contact-title">CONTACT THE <em>ENTERTAINER</em></h2>
<div class="abs inp" style="left:80px;top:2020px;width:310px">First Name</div>
<div class="abs inp" style="left:410px;top:2020px;width:310px">Last Name</div>
<div class="abs inp" style="left:80px;top:2070px;width:310px">Phone</div>
<div class="abs inp" style="left:410px;top:2070px;width:310px">Email</div>
<div class="abs inp" style="left:80px;top:2120px;width:640px;height:170px">Message</div>
<div class="abs cbtn" style="left:80px;top:2310px;width:80px">SEND</div>
<div class="abs cbtn" style="left:245px;top:2310px;width:170px">REQUEST A CALL BACK</div>
<svg class="abs" style="left:730px;top:2020px" width="30" height="270" viewBox="0 0 30 270"><path d="M2 2h10v124l14 9-14 9v124H2" fill="none" stroke="#fff" stroke-width="2"/></svg>
<div class="abs info" style="top:2020px"><div class="info-ico"><svg width="20" height="26" viewBox="0 0 20 26"><path d="M10 1a9 9 0 0 1 9 9c0 7-9 15-9 15S1 17 1 10a9 9 0 0 1 9-9z" fill="#fff"/><circle cx="10" cy="10" r="3.5" fill="#1f1f1f"/></svg></div><div><b style="color:var(--dark)">POP &amp; TWIST SHOWS</b><br>Lorem Ipsum, Dolor Sent<br>City Code - 1234567</div></div>
<div class="abs info" style="top:2120px"><div class="info-ico"><svg width="22" height="22" viewBox="0 0 24 24"><path d="M6.6 10.8a15 15 0 0 0 6.6 6.6l2.2-2.2c.3-.3.7-.4 1-.2 1.1.4 2.3.6 3.6.6.6 0 1 .4 1 1V20c0 .6-.4 1-1 1A17 17 0 0 1 3 4c0-.6.4-1 1-1h3.5c.6 0 1 .4 1 1 0 1.3.2 2.5.6 3.6.1.3 0 .7-.2 1z" fill="#fff"/></svg></div><div style="font-size:20px">123-456-7899</div></div>
<div class="abs info" style="top:2220px"><div class="info-ico"><svg width="24" height="18" viewBox="0 0 24 18"><rect x="1" y="1" width="22" height="16" fill="#fff"/><path d="M1 1l11 9 11-9" fill="none" stroke="#1f1f1f" stroke-width="2"/></svg></div><div>hello@popandtwistshows.com</div></div>

<footer class="abs footer"></footer>
<nav class="abs fnav"><a>HOME</a><a>ABOUT ME</a><a>CORPORATE SHOWS</a><a>PRIVATE FUNCTIONS</a><a>DIRECTING</a><a>REVIEWS</a><a>CONTACT ME</a></nav>
<div class="abs social"><i></i><i></i><i></i><i></i><i></i></div>
<div class="abs copy">Copyright Pop &amp; Twist Shows &nbsp;|&nbsp; All Rights Reserved</div>
</body>
</html>
```